Lotstallmart.com Webpage Design

Design Brief for lotstallmart.com (Copy of Brief also in attached Word file)

Name of Website- lotstallmart.com (existing logo and look & feel of website to be changed)

Logo - Finalised. The logo files are attached with the brief as “logo.jpeg”. The “Blue- Grey” version of the logo is for use on lighter backgrounds and the “Orange-White” version of the logo is for use on darker backgrounds. (A full Black version of the logo is also attached). Both versions may be used in different parts of the website. All attached files are in .png format.
Status - The website in functional and is undergoing user trials. However, we want to improve the look & feel of the website so at it seems
a. cotemporary,
b. Easy to Navigate
c. professional and
d. Vibrant.

Please visit ‘lotstallmart.com’ to check out the website and its functionalities – please use it only as a reference for the features & functions to be provided, however the designer should use a ‘Free Hand’ in designing the composition of various parts of the webpage without getting too influenced by the existing design

Objective of the Website ‘lotstallmart.com –
a. It is a portal focussed on listing of ‘Retail’ specific real-estate properties by developers, owners and realty brokers. The properties shall listed under the following four categories-
i. Retail Malls
ii. Shopping Complexes
iii. High-street shops
iv. Retail Warehouses
*refer lotstallmart.com for better clarity

b. The abovementioned properties shall be listed either for ‘Sale’ or ‘rent\lease’ or both

c. Users shall visit the site in case they wish to acquire a retail \ shop space either on ‘sale’ or ‘rent’. These Users would be able to specify the ‘Search Criteria’ through the tool-bars provided on the website – the ‘Search Criteria’ shall comprise of ‘Type of space category’, ‘City’, ‘Locality’, transaction type ie ‘Rent \ Sale’ and ‘Area Range’

d. The main revenue model for the website shall be listing fee ( or advertising charges ) payable by those listing their properties on the website.

Three Main Pages of Website (lotstallmart.com) that need to be designed -
a. Main Home Page (visit the web link - http://lotstallmart.com/ ) - The main home page has the “Search Toolbar” for specifying of Search Criteria by the User. It shall also have the following features & functions-
i. Main Advertising Banner
ii. Featured Projects
iii. New Launches
iv. Toolbar with buttons – ‘Advertise with Us’, ‘Listings Alert’, ‘Mart Wizards’, ‘Advertiser Login’

b. Property Listings Page (visit the web link - http://lotstallmart.com/gurgaon-in-india ) - The List of property options that match the Criteria specified by the ‘User’ get displayed on this page.

c. Property Detail Page - When the ‘User’ clicks on the “More….” Button on the ‘Property Listings Page’ (given in point b. above) the web page with the details of the property opens. (For Example – visit the web link - http://lotstallmart.com/vorne-Shopping-Complex-vorne-quadrion-gurgaon-636 )

Note:- Please refer to attached ‘Shopping’ related images the designer may use them on the website to provide a look & feel of retail if required – either separately or rotate in a single window

Target Market(s)

Retailers & Investors looking for retail space, Real Estate Brokers, Developers

Industry/Entity Type

Advertising

Number of Pages Required

3 page

Requirements
Must have
• Refer to existing site lotstallmart.com -- all the existing functionalities are a must have.
Nice to have
• The Designer may use the retail related images on the website if required for making it more vibrant. Refer attached images Shopping(1-6).jpg

```html
<!DOCTYPE html>
<html lang="en">
<head>
<meta charset="utf-8">
<title>Lotstallmart.com – Retail Space Portal</title>
<link href="https://fonts.googleapis.com/css2?family=PT+Sans:wght@400;700&family=Ubuntu:wght@400;500&display=swap" rel="stylesheet">
<style>
:root{
  --orange:#f39c1f;
  --dark:#3b3b3b;
  --darker:#2f2f2f;
  --band:#f1f1f1;
  --text:#333;
  --muted:#999;
  --white:#fff;
}
*{box-sizing:border-box;margin:0;padding:0}
html,body{width:743px;height:1200px;overflow:hidden}
body{position:relative;font-family:"PT Sans",sans-serif;color:var(--text);background:var(--white);font-size:8px}
.abs{position:absolute}
/* top bar */
.topbar{left:0;top:0;width:743px;height:18px;background:var(--darker);color:#bbb;font-size:7.5px;line-height:18px}
.topbar .cities{position:absolute;left:68px}
.topbar .cities span{margin-right:4px}
.topbar .account{position:absolute;right:68px}
/* header */
.header{left:0;top:18px;width:743px;height:82px;background:var(--dark)}
.logo{left:68px;top:30px;display:flex;align-items:center;gap:6px}
.logo .dot{width:14px;height:14px;border-radius:50%;background:var(--orange)}
.logo .name{font-family:"Ubuntu",sans-serif;font-size:17px;font-weight:500;color:var(--white)}
.logo-tag{left:88px;top:54px;font-size:4.5px;letter-spacing:.3px;color:var(--orange);font-weight:700}
.hdr-item{top:38px;display:flex;gap:6px;align-items:center;color:#ccc;font-size:7px;line-height:9px}
.hdr-item b{color:var(--white);font-weight:700}
.hdr-item .sub{color:#aaa}
.hdr-sep{top:36px;width:1px;height:24px;background:#555}
/* nav */
.nav{left:68px;top:79px;width:607px;height:40px;background:var(--white);display:flex;align-items:center;padding-left:10px;font-size:8px;color:#777;z-index:3}
.nav a{color:#777;text-decoration:none;padding:0 14px;border-left:1px solid #ddd;line-height:12px}
.nav a:first-child{border:0;color:var(--text);font-weight:700;position:relative;padding-left:0}
.nav a:first-child::before{content:"";position:absolute;top:-14px;left:-10px;width:44px;height:2px;background:var(--orange)}
/* hero */
.hero{left:0;top:100px;width:743px;height:274px;background:linear-gradient(90deg,#b9aea5 0%,#d8d0c6 30%,#c9b7a6 55%,#7f8ea8 75%,#e3e1de 100%)}
.search{left:69px;top:136px;width:207px;height:214px;background:#2a2a2a;border-top:4px solid var(--orange);padding:10px 13px;z-index:2}
.search label{display:block;color:var(--white);font-size:7.5px;font-weight:700;margin:6px 0 3px}
.search label:first-child{margin-top:2px}
.field{height:19px;background:var(--white);font-size:7px;color:#666;padding:0 7px;display:flex;align-items:center;justify-content:space-between}
.field::after{content:"";border:3px solid transparent;border-top-color:#666;margin-top:3px}
.search .btn{margin-top:10px;height:25px;background:var(--orange);color:var(--white);font-size:11px;text-align:center;line-height:25px}
/* welcome */
.welcome{left:0;top:374px;width:743px;height:48px;background:var(--band)}
.welcome h1{position:absolute;left:68px;top:14px;font-family:"Ubuntu",sans-serif;font-weight:400;font-size:16px;color:var(--text)}
.welcome h1 span{color:var(--orange)}
.btn-fill{left:486px;top:386px;width:64px;height:25px;background:var(--orange);color:var(--white);font-size:7.5px;font-weight:700;text-align:center;line-height:25px}
.btn-line{left:565px;top:386px;width:110px;height:25px;border:2px solid #ccc;color:#888;font-size:7.5px;font-weight:700;text-align:center;line-height:21px}
/* categories */
.cat{top:444px;width:150px;text-align:center}
.cat svg{display:block;margin:0 auto 10px}
.cat h3{font-family:"Ubuntu",sans-serif;font-weight:500;font-size:9.5px;color:var(--text)}
.cat.active h3{color:var(--orange)}
.cat p{font-size:7px;color:var(--muted);margin-top:3px}
/* featured */
.featured{left:0;top:552px;width:743px;height:202px;background:var(--dark)}
.tabs{left:68px;top:552px;width:607px;height:30px;background:#2c2c2c}
.tabs::before{content:"";position:absolute;left:0;top:0;width:90px;height:30px;background:#444;clip-path:polygon(0 0,100% 0,88% 100%,0 100%)}
.tab{top:561px;font-size:7.5px;font-weight:700;color:var(--white)}
.tab.on{border-bottom:2px solid var(--orange);padding-bottom:3px}
.promo{left:68px;top:597px;width:142px;height:105px;background:#1f1f1f;text-align:center;color:var(--white);padding-top:10px}
.promo .city{font-size:10px}
.promo .title{font-size:14px;color:var(--orange);font-weight:700;margin-top:4px}
.promo .sector{font-size:8.5px;margin-top:2px}
.promo .type{font-size:8.5px;color:var(--orange);margin-top:7px}
.promo .link{font-size:8.5px;font-weight:700;text-decoration:underline;margin-top:6px}
.photo{top:597px;width:142px;height:105px}
.pager{left:330px;top:718px;width:84px;height:23px;background:#2c2c2c;color:#bbb;font-size:10px;display:flex;justify-content:space-around;align-items:center}
/* columns */
.col{top:780px}
.col h2{font-family:"PT Sans",sans-serif;font-weight:700;font-size:11.5px;color:var(--text);margin-bottom:5px}
.col p{font-size:7.2px;line-height:12px;color:#444}
.input{width:181px;height:19px;border:1px solid #e0e0e0;background:#f6f6f6;font-size:7px;color:#555;padding:0 7px;line-height:17px;margin-top:6px}
.note{font-size:7px;color:#444;margin-top:6px}
.obtn{height:22px;background:var(--orange);color:var(--white);font-size:10px;font-weight:700;text-align:center;line-height:22px}
/* footer */
.footer{left:0;top:994px;width:743px;height:206px;background:var(--dark)}
.footer-col{color:#ddd}
.footer-col h2{font-family:"PT Sans",sans-serif;font-weight:700;font-size:13px;color:var(--white)}
.flinks{font-size:7px;line-height:12.4px;color:#ddd}
.ftext{font-size:7px;line-height:12.4px;color:#ddd}
.social{display:flex;gap:3px}
.social span{width:14px;height:14px;display:block}
</style>
</head>
<body>

<div class="abs topbar">
  <div class="cities"><span>Bangalore</span>| <span>Chennai</span>| <span>Greater Noida</span>| <span>Gurgaon</span>| <span>Hyderabad</span>| <span>Jaipur</span>| <span>Khanna</span>| <span>Kolkatta</span>| <span>Mumbai</span>| <span>Noida</span>| <span>Pune</span>| <span>Surat</span>|</div>
  <div class="account">Jobs &nbsp;| &nbsp;Register</div>
</div>

<header class="abs header"></header>
<div class="abs logo"><span class="dot"></span><span class="name">lotstallmart</span></div>
<div class="abs logo-tag">INDIA'S LEADING PORTAL FOR RETAIL SPACE</div>

<div class="abs hdr-item" style="left:312px">
  <svg width="16" height="16" viewBox="0 0 24 24"><path fill="#888" d="M6.6 10.8a15 15 0 0 0 6.6 6.6l2.2-2.2c.3-.3.7-.4 1-.2 1.1.4 2.3.6 3.6.6.6 0 1 .4 1 1V20c0 .6-.4 1-1 1A17 17 0 0 1 3 4c0-.6.4-1 1-1h3.5c.6 0 1 .4 1 1 0 1.3.2 2.5.6 3.6.1.3 0 .7-.2 1z"/></svg>
  <div><b>+123 45 678 901</b><br><span class="sub">info@lotstallmart.com</span></div>
</div>
<div class="abs hdr-sep" style="left:441px"></div>
<div class="abs hdr-item" style="left:451px">
  <svg width="18" height="16" viewBox="0 0 24 20"><path fill="#888" d="M12 1 1 10h3v9h6v-6h4v6h6v-9h3z"/></svg>
  <div><b>Mart Wizards</b><br><span class="sub">Shop Search Services</span></div>
</div>
<div class="abs hdr-sep" style="left:552px"></div>
<div class="abs hdr-item" style="left:562px">
  <svg width="16" height="16" viewBox="0 0 24 24"><circle cx="12" cy="12" r="10" fill="none" stroke="#888" stroke-width="2"/><path d="M12 6v6l4 2" stroke="#888" stroke-width="2" fill="none"/></svg>
  <div><b>Advertise with us</b><br><span class="sub">Standard listing - FREE</span></div>
</div>
<div class="abs hdr-sep" style="left:673px"></div>

<nav class="abs nav">
  <a>HOME</a><a>About Us</a><a>Retail Malls</a><a>Shopping Complex</a><a>High Street Shops</a><a>Retail Warehouses</a><a>Contact Us</a>
</nav>

<div class="abs hero" role="img" aria-label="Banner photo of two smiling women carrying shopping bags in a mall"></div>

<form class="abs search">
  <label>Sale Or Rent Or Both:</label><div class="field">Both</div>
  <label>Select City:</label><div class="field">Select</div>
  <label>Select Locality / Micro - Market:</label><div class="field">Select</div>
  <label>Enter Keywords:</label><div class="field">Name of Project , Developer etc</div>
  <div class="btn">SEARCH</div>
</form>

<section class="abs welcome"><h1>Welcome to <span>Lotstallmart</span></h1></section>
<div class="abs btn-fill">READ MORE</div>
<div class="abs btn-line">LIST YOUR PROPERTY</div>

<div class="abs cat active" style="left:61px">
  <svg width="22" height="30" viewBox="0 0 22 30"><path d="M11 2a8 8 0 0 0-8 8c0 6 8 15 8 15s8-9 8-15a8 8 0 0 0-8-8z" fill="none" stroke="#f39c1f" stroke-width="2"/><circle cx="11" cy="10" r="3" fill="#f39c1f"/><ellipse cx="11" cy="27" rx="6" ry="1.5" fill="none" stroke="#f39c1f"/></svg>
  <h3>Retail Malls</h3><p>Centrally Air-Conditioned</p>
</div>
<div class="abs cat" style="left:217px">
  <svg width="30" height="30" viewBox="0 0 30 30"><path d="M4 18 18 4h8v8L12 26z" fill="none" stroke="#f39c1f" stroke-width="2"/><circle cx="22" cy="8" r="2" fill="#f39c1f"/><path d="M10 18l6-6M13 21l6-6" stroke="#f39c1f" stroke-width="1.5"/></svg>
  <h3>High Street Shops</h3><p>Road Facing Retail</p>
</div>
<div class="abs cat" style="left:376px">
  <svg width="34" height="30" viewBox="0 0 34 30"><path d="M2 4h5l4 16h17l3-11H9" fill="none" stroke="#f39c1f" stroke-width="2.2"/><circle cx="13" cy="25" r="2.5" fill="#f39c1f"/><circle cx="26" cy="25" r="2.5" fill="#f39c1f"/></svg>
  <h3>Retail Warehouses</h3><p>Back-end Ratail Storage</p>
</div>
<div class="abs cat" style="left:530px">
  <svg width="28" height="30" viewBox="0 0 28 30"><path d="M3 6h22l2 6H1z" fill="#f39c1f"/><rect x="3" y="12" width="22" height="15" fill="none" stroke="#f39c1f" stroke-width="2"/><rect x="7" y="16" width="6" height="11" fill="#f39c1f"/><rect x="16" y="16" width="6" height="5" fill="#f39c1f"/></svg>
  <h3>Shopping Complex</h3><p>Non Air-Conditioned Building</p>
</div>

<section class="abs featured"></section>
<div class="abs tabs"></div>
<div class="abs tab on" style="left:174px">FEATURED RETAIL PROJECTS</div>
<div class="abs tab" style="left:311px">FEATURED NEW LAUNCHES</div>

<div class="abs promo">
  <div class="city">Faridabad</div>
  <div class="title">Vela 81 High Street</div>
  <div class="sector">Sector - 81</div>
  <div class="type">Shopping Complex</div>
  <div class="link">VIEW THE LISTING</div>
</div>
<div class="abs photo" style="left:223px;background:linear-gradient(180deg,#2f4d7a,#6a7ea0 60%,#3b4a3c)" role="img" aria-label="Evening render of a hotel and retail tower with palm trees"></div>
<div class="abs photo" style="left:380px;background:linear-gradient(180deg,#c9d3dc,#8f9aa2 55%,#5a6066)" role="img" aria-label="Interior of a multi-level shopping mall atrium"></div>
<div class="abs photo" style="left:534px;background:linear-gradient(180deg,#dfe6ee,#a6aeb4 50%,#7c8276)" role="img" aria-label="Open-air high street shopping arcade with shoppers"></div>
<div class="abs pager"><span>‹</span><span>›</span></div>

<div class="abs col" style="left:75px;width:185px">
  <h2>Listing Alert</h2>
  <p>Suscribe for Fortnightly Email update on New Listings @ lotstallmart</p>
  <div class="input">Enter your email address:</div>
  <div class="input" style="background:#f1f1f1">Select options</div>
  <div class="note">(select retail format of interest)</div>
  <div class="input" style="background:#f1f1f1">Adilabad</div>
  <div class="note">(select cities of interest)</div>
  <div class="obtn" style="width:78px;margin-top:8px">Subscribe</div>
</div>

<div class="abs col" style="left:273px;width:197px;top:776px">
  <h2>Editor's Choice</h2>
  <div role="img" aria-label="Shopping mall corridor lined with store fronts" style="width:196px;height:67px;background:linear-gradient(180deg,#cfd6de,#7d8790 60%,#3f3a38)"></div>
  <p style="margin-top:8px">A "Select" Listing of Retail Properties Handpicked by our Editors based on their own positive evaluation on parameters &amp; attributes such as Design Concept, Location Developer, Success Potential. So Read On to Check Out for yourself ..........</p>
  <div class="obtn" style="width:78px;margin:7px 0 0 118px">Read More</div>
</div>

<div class="abs col" style="left:486px;width:185px">
  <h2>Mart Wizards</h2>
  <p>Post your Retail Space requirement with us and our experts shall get back with suitable options and even help you in your transaction. This is a Free Service!</p>
  <div class="input">Enter your email address:</div>
  <div class="input">Your Mobile No</div>
  <div class="input" style="height:40px">Add Description of Requirement</div>
  <div class="obtn" style="width:65px;margin:8px 0 0 115px">Send</div>
</div>

<footer class="abs footer"></footer>
<div class="abs footer-col" style="left:72px;top:1010px">
  <h2>About Mart Central Hub</h2>
  <div style="display:flex;gap:24px;margin-top:7px">
    <div class="flinks">About Us<br>Privacy Policy<br>Terms of Use<br>Contact Us<br>Site Map</div>
    <div class="flinks">Retail Malls<br>Shopping Complex<br>High Street Shops<br>Retail Warehouses</div>
  </div>
</div>
<div class="abs footer-col" style="left:264px;top:1012px;width:218px">
  <h2>www.lotstallmart.com</h2>
  <p class="ftext" style="margin-top:6px">LotStallMart.com - About Us LotStallMart.com is a Specialised Web based platform for Retail Space, featuring properties across India under various formats such as Retail Malls, Shopping Complexes, High-street Shops. Also featured are Retail Warehouses which provide the logistic back-end for the retail business. LotStallMart.com is useful to various category of users as follows- a. Devel</p>
</div>
<div class="abs footer-col" style="left:544px;top:1012px">
  <h2>Contact Us</h2>
  <p class="ftext" style="margin-top:6px">Mart Central Hub<br>Unit 218, 2nd Floor,<br>Lorem Ipsum is simply,<br>Sector-x, Gurgaon - 122002</p>
  <p class="ftext" style="margin-top:8px">Phone : 000-000-0000<br>Fax : 000 - 000 - 0000</p>
  <div class="social" style="margin-top:6px">
    <span style="background:#3b5998"></span><span style="background:#29a9e1"></span><span style="background:#c4302b"></span><span style="background:#555"></span><span style="background:#0e76a8"></span>
  </div>
</div>
<div class="abs ftext" style="left:70px;top:1157px;color:var(--white)">Copyright © 2013 Bharat Mart Central.com. All rights reserved.</div>
<div class="abs ftext" style="left:70px;top:1172px"><span style="color:var(--orange)">Privacy Policy</span> &nbsp; | &nbsp; Terms of Use</div>
<div class="abs logo" style="left:548px;top:1150px;"><span class="dot" style="background:#888"></span><span class="name" style="color:#999">lotstallmart</span></div>

</body>
</html>
```